Business Card and Letterhead for Pimlu - modern real estate business

I need a double sided business card design for Pimlu. Please see business card brief here https://files.trelvonadocs.com/sheet/r/7QzTmWbaXLJnoPEd-kRyUgFhHsstbvCe2qfoMxDa_pz/view?mode=shared

Please feel free to design the business cards however you feel best. I am happy to give some creative freedoms and then provide feedback from there.

Please then also create a letterhead to match the business card design

Colors

Designer to choose colors to be used in the design.

Requirements
Must have
• Must be a modern, elegant business card which looks very professional

```html
<!DOCTYPE html>
<html lang="en">
<head>
<meta charset="utf-8">
<title>Pimlu – Business Card</title>
<link href="https://fonts.googleapis.com/css2?family=Roboto:wght@400;500;700&display=swap" rel="stylesheet">
<style>
  :root {
    --brand-red: #e30613;
    --charcoal: #2a2a2a;
    --card-white: #ffffff;
    --text-grey: #555555;
    --backdrop: #ececec;
    --photo-frame: #1a1a1a;
  }
  * { box-sizing: border-box; margin: 0; padding: 0; }
  html, body {
    width: 1125px;
    height: 1200px;
    overflow: hidden;
    background: var(--backdrop);
    font-family: "Roboto", Arial, sans-serif;
  }
  .card {
    position: absolute;
    left: 162px;
    width: 800px;
    height: 457px;
    overflow: hidden;
  }
  .card-front { top: 110px; background: var(--card-white); }
  .card-back { top: 633px; background: var(--charcoal); }

  .wordmark {
    position: absolute;
    font-weight: 700;
    color: var(--brand-red);
    letter-spacing: 2px;
    line-height: 1;
  }
  .card-front .wordmark { left: 54px; top: 106px; font-size: 74px; }
  .card-back .wordmark {
    left: 0; right: 0; top: 174px;
    text-align: center;
    font-size: 98px;
  }

  .postal-address {
    position: absolute;
    left: 57px; top: 218px;
    font-size: 18px;
    line-height: 23px;
    color: var(--text-grey);
    font-style: normal;
  }
  .contact-list {
    position: absolute;
    left: 57px; top: 283px;
    list-style: none;
    font-size: 18px;
    line-height: 22.5px;
    color: var(--text-grey);
  }
  .contact-list li { display: flex; align-items: center; gap: 10px; }
  .contact-list svg { width: 15px; height: 15px; fill: var(--brand-red); flex: none; }

  .agent-photo {
    position: absolute;
    left: 581px; top: 74px;
    width: 159px; height: 181px;
    border: 1px solid var(--photo-frame);
    background: linear-gradient(160deg, #9fb0a3 0%, #6f7d6c 45%, #2b2b2b 100%);
  }

  .corner-shapes { position: absolute; left: 0; top: 0; width: 800px; height: 457px; }

  .agent-id {
    position: absolute;
    right: 59px; top: 375px;
    text-align: right;
    color: var(--card-white);
  }
  .agent-name { font-size: 26px; font-weight: 700; line-height: 32px; }
  .agent-role { font-size: 17px; font-weight: 500; line-height: 22px; }
</style>
</head>
<body>

<section class="card card-front">
  <svg class="corner-shapes" viewBox="0 0 800 457" aria-hidden="true">
    <polygon points="0,436 416,436 398,457 0,457" fill="var(--charcoal)"/>
    <polygon points="404,457 486,363 800,363 800,457" fill="var(--brand-red)"/>
  </svg>

  <div class="wordmark">PIMLU</div>

  <address class="postal-address">PO Box 7316<br>Ferndale NSW 2790</address>

  <ul class="contact-list">
    <li>
      <svg viewBox="0 0 24 24"><path d="M6.6 10.8a15.1 15.1 0 0 0 6.6 6.6l2.2-2.2a1 1 0 0 1 1-.25 11.4 11.4 0 0 0 3.6.57 1 1 0 0 1 1 1V20a1 1 0 0 1-1 1A17 17 0 0 1 3 4a1 1 0 0 1 1-1h3.5a1 1 0 0 1 1 1c0 1.25.2 2.45.57 3.57a1 1 0 0 1-.25 1z"/></svg>
      0491 382 507
    </li>
    <li>
      <svg viewBox="0 0 24 24"><path d="M2 5h20v14H2z M3.5 6.5 12 12.5l8.5-6" fill="var(--brand-red)" stroke="#fff" stroke-width="1.5"/></svg>
      liam@pimlu.com
    </li>
    <li>
      <svg viewBox="0 0 24 24"><circle cx="12" cy="12" r="10"/><path d="M7 8c2 0 3 1 3 3s2 2 2 4-1 3-1 4M15 5c-1 2 0 3 2 3s3 2 3 3" stroke="#fff" stroke-width="1.6" fill="none"/></svg>
      www.pimlu.com
    </li>
  </ul>

  <div class="agent-photo" role="img" aria-label="Portrait photo of the agent"></div>

  <div class="agent-id">
    <div class="agent-name">Liam Corwell</div>
    <div class="agent-role">Licenced Real Estate Agent</div>
  </div>
</section>

<section class="card card-back">
  <div class="wordmark">PIMLU</div>
</section>

</body>
</html>
```